Wordpress Design for a Digital Management Consulting Business

I need a simple Wordpress Design and someone to set it up for a new boutique management consulting business called Quillon Advisory that specialises in providing strategic advice to help grow digital businesses. It covers business strategy, marketing strategy, digital strategy, web product development, marketing campaigns, social, search, etc. From strategy to implementation.

URL is: quillonadvisory.com.au

My professional background is here: au.linkedin.com/in/hollyprenwick

Competitors: other boutique digital/marketing management consulting businesses in Australia

The logos, colours and fonts are attached.

I would like the site to convey a business that is Smart/intelligent, Contemporary, Progressive, Digital, Energetic, Friendly.

The objective of the site is to educate visitors about what Quillon Advisory does and encourage them to contact me for more information. It will be very light on content.

Target Market(s)

CEOs/Managing Directors, General Managers, Marketing Directors

Industry/Entity Type

Management Consulting

Font styles to use
Sans Serif

Colors
e34197
5c5c5c
000000

Requirements
Must have
• Site design requirements:
• Choose an appropriate Wordpress template, set it up for me and let me be able to edit it ongoing.
• It should use lots of images - these can be inspirational and not necessarily tied directly to the work
• Pink should feature, but not be the dominant colour.
• Site structure should be:
• 1. Home page - image led with horizontal navigation. Text beneath and images to describe the services.
• 2. About page - with space to write text and insert a picture of the Director
• 3. Services - with space to highlight services either as a list or graphically with text
• 4. Contact page - with space to write text and add email links, etc.
• Should have horizontal navigation
• It should have the flexibility to add another page
Nice to have
• Use the tree icon somehow in the design - consider in the background enlarged
• Use pink, grey, black from logo. Can introduce another complimentary colour if necessary.
• Can introduce another complimentary font to go with the logo font.
Should not have
• Use cliched business images and icons, eg. business suits, hand shakes, business men, business ties.

```html
<!DOCTYPE html>
<html lang="en">
<head>
<meta charset="utf-8">
<title>Quillon Advisory</title>
<link href="https://fonts.googleapis.com/css2?family=Open+Sans:wght@300;400;600&display=swap" rel="stylesheet">
<style>
:root{
  --pink:#e34197;
  --grey:#5c5c5c;
  --black:#000;
  --dark:#3b3b3b;
  --footer:#262626;
  --light:#f4f4f4;
  --text:#555;
}
*{box-sizing:border-box;margin:0;padding:0}
html,body{width:682px;height:1200px;overflow:hidden;background:#fff}
body{font-family:"Open Sans",Arial,sans-serif;color:var(--text);font-size:7px;line-height:1.45}
.page{position:relative;width:682px;height:1200px}
.wrap{position:relative;width:566px;margin:0 auto}

/* header */
.site-header{height:63px;display:flex;align-items:center;justify-content:space-between;padding:0 58px}
.brand{display:flex;align-items:center;gap:8px;color:var(--grey);font-size:17px;font-weight:400;letter-spacing:1px;line-height:1}
.brand-mark{width:24px;height:24px;border-radius:50%;background:var(--pink)}
.main-nav{display:flex;gap:0}
.main-nav a{font-size:7.5px;color:var(--grey);text-decoration:none;padding:6px 12px;border-left:1px solid #ddd}
.main-nav a:first-child{border-left:0}
.main-nav a.active{color:var(--pink)}

/* hero */
.hero{position:relative;height:220px;background:linear-gradient(100deg,#f2f2f2 0%,#e3e6e8 45%,#aebfc9 75%,#8fa6b2 100%)}
.hero-intro{position:absolute;left:58px;top:50px;width:230px}
.hero-intro h1{font-weight:400;font-size:21px;color:#222;line-height:1.2;margin-bottom:6px}
.hero-intro p{font-size:8.5px;color:#555;line-height:1.45}

/* section titles */
.section-title{font-weight:300;font-size:23px;color:#333;line-height:1}

/* services */
.services{height:283px;padding-top:30px}
.card-row{display:flex;gap:21px;margin-top:18px}
.card{width:175px}
.card-image{height:83px}
.card h3{font-weight:400;font-size:11.5px;color:var(--pink);margin:10px 0 3px}
.card p{font-size:6.8px;color:#666}
.read-more{display:inline-block;font-size:7px;color:#333;font-weight:600;margin-top:7px}

/* what we do */
.what-we-do{height:285px;background:var(--dark);padding-top:30px}
.what-we-do .section-title{color:#fff}
.feature-row{display:flex;gap:21px;margin-top:17px}
.feature{width:175px}
.feature-image{height:89px;border:2px solid var(--pink)}
.feature h3{font-weight:400;font-size:11.5px;color:#fff;line-height:1.15;margin:9px 0 4px;min-height:28px}
.feature p{font-size:6.8px;color:#c8c8c8}
.btn{display:inline-block;background:var(--pink);color:#fff;font-size:7px;padding:3px 9px;margin-top:9px}

/* article */
.articles{height:173px;padding-top:28px}
.article-row{display:flex;gap:22px;margin-top:14px}
.article{width:272px;display:flex;gap:10px}
.article-image{width:90px;height:57px;flex:none}
.article-date{font-size:7px;color:#333;font-weight:600}
.article p{font-size:6.6px;color:#666}
.article .byline{color:var(--pink);font-size:6.4px;margin-top:2px}

/* footer */
.site-footer{height:147px;background:var(--footer);padding-top:18px;color:#bbb}
.footer-cols{display:flex}
.footer-col h4{font-weight:300;font-size:17px;color:#fff;line-height:1;margin-bottom:10px}
.footer-col ul{list-style:none}
.footer-col li{font-size:6.8px;line-height:1.9;color:#bbb}
.footer-col li::before{content:"›";margin-right:5px;color:#888}
.col-links{width:110px}
.col-services{width:288px}
.service-lists{display:flex;gap:40px}
.col-contact h4{margin-bottom:12px}
.contact-line{display:flex;align-items:center;gap:8px;font-size:6.8px;margin-bottom:9px}
.contact-line svg{flex:none}
.social{display:flex;gap:7px;margin-top:4px}
.social span{width:13px;height:13px;border-radius:50%;background:#555}

.copyright{height:34px;background:var(--pink);color:#fff;font-size:6.8px;display:flex;align-items:center;justify-content:center}
</style>
</head>
<body>
<div class="page">

  <header class="site-header">
    <div class="brand"><span class="brand-mark"></span>Quillon Advisory</div>
    <nav class="main-nav">
      <a class="active">HOME</a><a>SERVICES</a><a>ABOUT</a><a>CLIENTS</a><a>CONTACT US</a>
    </nav>
  </header>

  <section class="hero" role="img" aria-label="Photo of a hand working on a tablet with charts">
    <div class="hero-intro">
      <h1>Quillon Advisory</h1>
      <p>Boutique management consulting company assisting digital businesses across business, product and marketing strategy.</p>
    </div>
  </section>

  <section class="services">
    <div class="wrap">
      <h2 class="section-title">Our Services</h2>
      <div class="card-row">
        <article class="card">
          <div class="card-image" role="img" aria-label="Photo of a hand touching digital interface graphics" style="background:linear-gradient(135deg,#f3d3e3,#c7d7ea 60%,#8fa9c6)"></div>
          <h3>Digital Strategy</h3>
          <p>Lorem ipsum dolor sit amet, consectetur adipisicing elit, sed eiusmod tempor incididunt ut labore et dolore magna aliqua...</p>
          <span class="read-more">Read more.</span>
        </article>
        <article class="card">
          <div class="card-image" role="img" aria-label="Photo of a person working at a desk" style="background:linear-gradient(135deg,#e8e8e8,#b9b9b9 55%,#6d6d6d)"></div>
          <h3>Marketing Strategy</h3>
          <p>Lorem ipsum dolor sit amet, consectetur adipisicing elit, sed eiusmod tempor incididunt ut labore et dolore magna aliqua...</p>
          <span class="read-more">Read more.</span>
        </article>
        <article class="card">
          <div class="card-image" role="img" aria-label="Photo of hands on a blue digital touchscreen" style="background:linear-gradient(135deg,#1d3a66,#3f79b4 55%,#9fc3e6)"></div>
          <h3>Digital Transformation</h3>
          <p>Lorem ipsum dolor sit amet, consectetur adipisicing elit, sed eiusmod tempor incididunt ut labore et dolore magna aliqua...</p>
          <span class="read-more">Read more.</span>
        </article>
      </div>
    </div>
  </section>

  <section class="what-we-do">
    <div class="wrap">
      <h2 class="section-title">What we do</h2>
      <div class="feature-row">
        <article class="feature">
          <div class="feature-image" role="img" aria-label="Photo of a team meeting around a table" style="background:linear-gradient(135deg,#d9c7b8,#9b8a7d 60%,#5e5450)"></div>
          <h3>Strategic Thinking</h3>
          <p>Lorem Ipsum has been the industry's standard ipsum dolor sit amet, consectetur adipisicing elit, sed eiusmod tempor.</p>
          <span class="btn">Read more</span>
        </article>
        <article class="feature">
          <div class="feature-image" role="img" aria-label="Photo of a laptop with charts on a desk" style="background:linear-gradient(135deg,#f1f1f1,#c9c9c9 55%,#8b8b8b)"></div>
          <h3>Analytical Approach</h3>
          <p>Lorem Ipsum has been the industry's standard ipsum dolor sit amet, consectetur adipisicing elit, sed eiusmod tempor.</p>
          <span class="btn">Read more</span>
        </article>
        <article class="feature">
          <div class="feature-image" role="img" aria-label="Photo of colleagues collaborating at a desk" style="background:linear-gradient(135deg,#c9d6e0,#8a9aa8 55%,#4e5966)"></div>
          <h3>End to end project Management</h3>
          <p>Lorem Ipsum has been the industry's standard ipsum dolor sit amet, consectetur adipisicing elit, sed eiusmod tempor.</p>
          <span class="btn">Read more</span>
        </article>
      </div>
    </div>
  </section>

  <section class="articles">
    <div class="wrap">
      <h2 class="section-title">Article</h2>
      <div class="article-row">
        <article class="article">
          <div class="article-image" role="img" aria-label="Photo of a business meeting" style="background:linear-gradient(135deg,#dcdcdc,#8f8f8f)"></div>
          <div>
            <div class="article-date">26 May '14, 08:00pm in Magazine</div>
            <p>When an unknown printer took a galley of type and scrambled it to make a type specimen book.</p>
            <p class="byline">- Dana Whitlock, Partner MRH</p>
          </div>
        </article>
        <article class="article">
          <div class="article-image" role="img" aria-label="Photo of a business meeting" style="background:linear-gradient(135deg,#dcdcdc,#8f8f8f)"></div>
          <div>
            <div class="article-date">26 May '14, 08:00pm in Magazine</div>
            <p>When an unknown printer took a galley of type and scrambled it to make a type specimen book.</p>
            <p class="byline">- Dana Whitlock, Partner MRH</p>
          </div>
        </article>
      </div>
    </div>
  </section>

  <footer class="site-footer">
    <div class="wrap footer-cols">
      <div class="footer-col col-links">
        <h4>Links</h4>
        <ul><li>Home</li><li>Our Services</li><li>About Us</li><li>Clients</li><li>Contact Us</li></ul>
      </div>
      <div class="footer-col col-services">
        <h4>Services</h4>
        <div class="service-lists">
          <ul><li>Business Strategy</li><li>Digital Strategy</li><li>Marketing Strategy</li><li>Product Strategy</li><li>Marketing Campaigns</li></ul>
          <ul><li>Product Management</li><li>Digital Marketing</li><li>Social Web Strategy</li><li>Content Marketing</li><li>New Product launches</li></ul>
        </div>
      </div>
      <div class="footer-col col-contact">
        <h4>Contact Us</h4>
        <div class="contact-line">
          <svg width="11" height="11" viewBox="0 0 24 24"><path fill="#ccc" d="M6.6 10.8a15.1 15.1 0 0 0 6.6 6.6l2.2-2.2c.3-.3.7-.4 1-.2 1.1.4 2.3.6 3.6.6.6 0 1 .4 1 1V20c0 .6-.4 1-1 1A17 17 0 0 1 3 4c0-.6.4-1 1-1h3.5c.6 0 1 .4 1 1 0 1.3.2 2.5.6 3.6.1.3 0 .7-.2 1z"/></svg>
          <span>Holly Prenwick 0412 580 364</span>
        </div>
        <div class="contact-line">
          <svg width="11" height="11" viewBox="0 0 24 24"><rect x="2" y="5" width="20" height="14" rx="1" fill="none" stroke="#ccc" stroke-width="2"/><path d="M2 6l10 7 10-7" fill="none" stroke="#ccc" stroke-width="2"/></svg>
          <span>holly@quillonadvisory.com.au</span>
        </div>
        <div class="social"><span></span><span></span><span></span><span></span><span></span></div>
      </div>
    </div>
  </footer>

  <div class="copyright">© 2015 Copyright Quillon Advisory. All Right Reserved</div>
</div>
</body>
</html>
```